Update the A4 Specials Page for Restaurant/Cafe

Provide a MINIMALIST attractive Specials page we can print weekly for our food and drink specials to give to our guests. Final design is to be provided in WORD Document so it can be easily edited by Manager. Should be black text and MINIMALIST to minimise ink usage as we print hundreds a week. We have UPLOADED the existing page as a template for you to update. Maybe logo can stay, see what you think. Or delete it and do something else. Keep it simple. Choose a good FONT. Could be a little playful with a cocktail ICON or something. Our existing menus can be seen at www.saltmeadowcafe.com.au and they are using font Alegreya. Please note we are unable to provide any feedback to designers, however we really do appreciate your time if you are submitting a design. Thank you for your participation.

```html
<!DOCTYPE html>
<html lang="en">
<head>
<meta charset="utf-8">
<title>Salt Meadow Cafe – Weekly Specials</title>
<link rel="stylesheet" href="https://fonts.googleapis.com/css2?family=Poppins:wght@400;500;600&display=swap">
<style>
  :root {
    --backdrop: #e6e7e9;
    --paper: #ffffff;
    --ink: #111111;
    --ink-soft: #444444;
    --band: #000000;
    --band-text: #ffffff;
    --seal: #8b1c24;
  }
  * { margin: 0; padding: 0; box-sizing: border-box; }
  html, body {
    width: 676px; height: 1200px; overflow: hidden;
    background: var(--backdrop);
    font-family: "Poppins", sans-serif;
    color: var(--ink);
  }
  .specials-page {
    position: absolute; left: 40px; top: 179px;
    width: 596px; height: 842px;
    background: var(--paper);
    box-shadow: 3px 4px 6px rgba(0,0,0,0.25);
  }
  .name-band {
    position: absolute; left: 48px; top: 0;
    width: 44px; height: 168px;
    background: var(--band);
    display: flex; align-items: center; justify-content: center;
  }
  .name-band span {
    display: block; transform: rotate(-90deg);
    white-space: nowrap;
    color: var(--band-text);
    font-weight: 600; font-size: 11px; letter-spacing: 0.5px;
  }
  .line {
    position: absolute; left: 0; width: 100%;
    text-align: center; white-space: nowrap;
  }
  .section-title { font-size: 18px; font-weight: 600; letter-spacing: 3.4px; line-height: 20px; }
  .item-name { font-size: 17px; font-weight: 400; letter-spacing: 2.2px; line-height: 20px; }
  .item-name.muted { color: var(--ink-soft); }
  .item-detail { font-size: 12px; line-height: 14px; }
  .price { font-size: 17px; font-weight: 600; line-height: 18px; }
  .seal {
    position: absolute; right: 42px; top: 723px;
    display: flex; align-items: center; gap: 10px;
  }
  .seal-name { font-size: 9px; font-weight: 500; letter-spacing: 1px; color: var(--ink); }
  .seal-mark { width: 80px; height: 80px; border-radius: 50%; background: var(--seal); }
</style>
</head>
<body>
  <main class="specials-page">
    <div class="name-band"><span>SALT MEADOW CAFE</span></div>

    <h1 class="line section-title" style="top:138px">WEEKLY SPECIALS</h1>
    <h2 class="line item-name" style="top:176px">CHICKEN FILO</h2>
    <p class="line item-detail" style="top:204px">Creamy Chicken with Pinenuts. wrapped in Filo Pastry.</p>
    <p class="line item-detail" style="top:223px">Served with Side Salad &amp; Zulu Sauce</p>
    <p class="line price" style="top:249px">$24</p>

    <h2 class="line item-name" style="top:286px">MINESTRONE SOUP</h2>
    <p class="line item-detail" style="top:313px">Served with Garlic Bread</p>
    <p class="line price" style="top:339px">$8</p>

    <h1 class="line section-title" style="top:396px">COCKTAIL SPECIAL</h1>
    <h2 class="line item-name muted" style="top:435px">PASSIONISTA</h2>
    <p class="line item-detail" style="top:463px">Vodka, Passionfruit Pulp, Mango Puree</p>
    <p class="line item-detail" style="top:482px">Top up with Ginger &amp; Lemon Kombucha</p>
    <p class="line price" style="top:509px">$17</p>

    <h1 class="line section-title" style="top:566px">CRAFT BEER SPECIAL</h1>
    <h2 class="line item-name muted" style="top:605px">CROOKED GECKO</h2>
    <p class="line item-detail" style="top:632px">PULP TIDE</p>
    <p class="line item-detail" style="top:651px">Tropical Pale Ale</p>
    <p class="line item-detail" style="top:670px">4.8% Alc.</p>
    <p class="line price" style="top:695px">$10</p>

    <div class="seal">
      <span class="seal-name">SALT MEADOW CAFE</span>
      <div class="seal-mark"></div>
    </div>
  </main>
</body>
</html>
```